The Marigold Venture WEBSITE DESIGN

Marigold is a not for profit working in international aid and development. The website needs to be lively not depressing,earthy rather than bling, have a dramatic impact over lightweight. It may be that a black and white with spot colour may be more impacting given the simplicity I want for the site. Marigold works in partnership with registered NGOs in Asia and Africa. At any one time it will have about five feature projects. The purpose is for people to be able to find out about the projects, the countries, the partner organisations, people's stories and then give people the opportunity to give their financial and volunteer support.

Target Market(s)

First World Donors
All ages but particularly 25 - 55

Industry/Entity Type

Human Rights

Number of Pages Required

5+ page

Font styles to use
Sans Serif

Requirements
Must have
• Simplicity
• Easy access to giving options
• Highlight stories both video and image + copy (sample in attachments)
• Lots of images over copy
Nice to have
• Interest
• Not boring
• May work in black and white with a spot colour or sepia look
Should not have
• Shiny new look
• Dont know how many pages or if it be coded or uncoded - makes no sense to me

```html
<!DOCTYPE html>
<html lang="en">
<head>
<meta charset="utf-8">
<title>The Marigold Venture</title>
<link href="https://fonts.googleapis.com/css2?family=Roboto:wght@400;500;700;900&display=swap" rel="stylesheet">
<style>
:root{
  --ink:#222;
  --text:#555;
  --muted:#888;
  --line:#d6d6d6;
  --spot:#e0792b;
  --grey-band:#ececec;
  --dark:#2b2b2b;
  --darker:#1f1f1f;
  --button:#5a5a5a;
  --play:#1a9bd7;
  --white:#fff;
}
*{box-sizing:border-box;margin:0;padding:0}
html,body{width:1200px;height:2684px;overflow:hidden}
body{font-family:"Roboto",Arial,sans-serif;color:var(--text);background:var(--white)}
.wrap{width:1000px;margin:0 auto;position:relative}
h2.section-title{font-weight:900;font-size:40px;color:var(--ink);letter-spacing:.5px;text-transform:uppercase}

/* header */
.site-header{height:168px;position:relative}
.brand{position:absolute;left:100px;top:52px;display:flex;align-items:center;gap:14px}
.brand-dot{width:56px;height:56px;border-radius:50%;background:var(--spot)}
.brand-name{font-weight:900;font-size:36px;color:var(--spot);letter-spacing:1px}
.search{position:absolute;right:100px;top:40px;display:flex;height:32px}
.search input{width:176px;border:1px solid var(--line);font:12px "Roboto",sans-serif;padding:0 10px;color:var(--muted)}
.search button{width:32px;border:1px solid var(--line);border-left:0;background:#f4f4f4;display:flex;align-items:center;justify-content:center}
.main-nav{position:absolute;right:100px;top:112px;display:flex;gap:38px}
.main-nav a{font-size:13px;font-weight:500;color:var(--muted);text-decoration:none;text-transform:uppercase;letter-spacing:.5px;padding-bottom:8px}
.main-nav a.active{color:var(--ink);border-bottom:3px solid var(--ink)}

/* hero */
.hero{height:312px;background:linear-gradient(180deg,#b8916a 0%,#8a4a38 45%,#6a3a3a 75%,#4f3e52 100%)}

/* about */
.about{height:680px;padding-top:60px}
.accordion{margin-top:28px}
.acc-item{border-bottom:1px solid var(--line);margin-bottom:26px;padding-bottom:0;position:relative}
.acc-head{display:flex;align-items:center;gap:12px;font-weight:700;font-size:17px;color:var(--ink);text-transform:uppercase;letter-spacing:.5px;padding-bottom:8px}
.acc-icon{width:14px;height:14px;border:2px solid var(--ink);position:relative}
.acc-head::after{content:"";position:absolute;left:0;bottom:-3px;width:110px;height:5px;background:var(--ink)}
.acc-item.open .acc-head::after{background:var(--spot)}
.acc-body{padding:22px 0 26px;font-size:14px;line-height:1.75;color:var(--text)}

/* projects */
.projects{height:540px;background:var(--grey-band);padding-top:110px}
.cards{display:flex;gap:50px;margin-top:34px}
.card{width:300px}
.card-image{height:180px}
.card-image.a{background:linear-gradient(160deg,#9db07a,#c49a5c 55%,#7c5a3c)}
.card-image.b{background:linear-gradient(160deg,#8a5a3a,#b6805a 50%,#4f3a2c)}
.card-image.c{background:linear-gradient(160deg,#a58a62,#c09a6e 50%,#6e5a44)}
.card p{font-size:13px;font-weight:500;color:var(--ink);line-height:1.45;margin:12px 0 14px}
.btn-small{display:inline-block;font-size:11px;padding:6px 14px;background:#d9d9d9;color:var(--ink);border:1px solid #c4c4c4}

/* stories */
.stories{height:620px;padding-top:68px}
.stories-grid{display:flex;gap:12px;margin-top:24px}
.video{width:500px;height:280px;position:relative;background:linear-gradient(170deg,#c6b89a,#8f7a5a 55%,#4e4638)}
.play{position:absolute;left:226px;top:116px;width:48px;height:48px;border-radius:50%;background:var(--play);display:flex;align-items:center;justify-content:center}
.story-list{flex:1;display:flex;flex-direction:column;gap:8px}
.story{display:flex;gap:16px;height:88px}
.story-thumb{width:110px;height:88px;flex:none}
.story-thumb.a{background:linear-gradient(160deg,#d6c08a,#8e7040)}
.story-thumb.b{background:linear-gradient(160deg,#9fae76,#5a6a3e)}
.story-thumb.c{background:linear-gradient(160deg,#b0946a,#6a5238)}
.story-text{font-size:13px;line-height:1.5;padding-top:6px;color:var(--text)}
.story-text strong{display:block;color:var(--ink);font-weight:700}
.support{display:flex;gap:20px;margin-top:32px}
.support-box{width:490px;height:140px;background:var(--dark);color:var(--white);padding:18px 22px}
.support-box h3{font-weight:900;font-size:24px;text-transform:uppercase;letter-spacing:.5px}
.support-box p{font-size:12px;line-height:1.5;color:#ccc;margin:8px 0 12px;width:380px}
.btn-outline{display:inline-block;font-size:11px;font-weight:500;text-transform:uppercase;border:1px solid var(--white);padding:5px 12px;color:var(--white)}

/* connect */
.connect{height:220px;text-align:center;padding-top:78px}
.connect h2{font-weight:900;font-size:38px;color:var(--ink);text-transform:uppercase}
.connect-buttons{display:flex;gap:20px;margin-top:26px}
.connect-btn{flex:1;height:44px;background:var(--button);color:var(--white);display:flex;align-items:center;justify-content:center;gap:12px;font-weight:500;font-size:15px;text-transform:uppercase;letter-spacing:.5px}

/* footer */
.site-footer{height:104px;background:var(--dark);color:#bbb;padding-top:14px}
.footer-cols{display:flex;gap:30px}
.footer-col h4{font-size:10px;font-weight:700;color:var(--white);text-transform:uppercase;margin-bottom:5px}
.footer-col ul{list-style:none;columns:3;column-gap:26px}
.footer-col.news ul{columns:2}
.footer-col li{font-size:9px;line-height:14px;white-space:nowrap}
.newsletter{margin-left:auto;width:200px}
.newsletter-form{display:flex;height:20px;margin-bottom:8px}
.newsletter-form span{flex:1;background:var(--white);font-size:9px;color:var(--muted);padding:4px 6px}
.newsletter-form b{width:42px;background:var(--button);font-size:9px;color:var(--white);text-align:center;padding-top:4px;font-weight:500}
.social{display:flex;gap:8px}
.social i{width:18px;height:18px;border-radius:50%;background:#777;display:block}
.copyright{height:40px;background:var(--darker);color:#999;font-size:10px}
.copyright .wrap{display:flex;align-items:center;height:40px}
.copyright .social{margin-left:auto}
</style>
</head>
<body>

<header class="site-header">
  <div class="brand"><span class="brand-dot"></span><span class="brand-name">MARIGOLD</span></div>
  <form class="search"><input value="Search"><button type="button"><svg width="12" height="12" viewBox="0 0 12 12"><circle cx="5" cy="5" r="3.6" fill="none" stroke="#666" stroke-width="1.6"/><line x1="7.6" y1="7.6" x2="11" y2="11" stroke="#666" stroke-width="1.6"/></svg></button></form>
  <nav class="main-nav">
    <a class="active">About Marigold</a><a>Current Projects</a><a>Stories</a><a>Giving</a><a>Contact</a>
  </nav>
</header>

<section class="hero" role="img" aria-label="Group photo of women from a partner community standing together outdoors"></section>

<section class="about">
  <div class="wrap">
    <h2 class="section-title">About Marigold</h2>
    <div class="accordion">
      <div class="acc-item open">
        <div class="acc-head"><span class="acc-icon"></span>Purpose</div>
        <div class="acc-body">Marigold works alongside registered local partners across Asia and Africa to support communities as they build lasting change. We fund practical projects in education, livelihoods and health, chosen and led by the people they serve. Every gift goes toward work that is transparent, accountable and shaped by local voices, so that families can grow stronger, children can learn and women can lead. We share the stories behind each project so our supporters can see what their generosity makes possible, and we invite everyone to give, volunteer and stand with our partners for the long term.</div>
      </div>
      <div class="acc-item"><div class="acc-head"><span class="acc-icon"></span>Values</div></div>
      <div class="acc-item"><div class="acc-head"><span class="acc-icon"></span>Meaning of Name</div></div>
      <div class="acc-item"><div class="acc-head"><span class="acc-icon"></span>Board</div></div>
    </div>
  </div>
</section>

<section class="projects">
  <div class="wrap">
    <h2 class="section-title">Current Projects</h2>
    <div class="cards">
      <article class="card">
        <div class="card-image a" role="img" aria-label="Women of a weaving cooperative seated together in Cambodia"></div>
        <p>Lotus Cambodia – silk weaving cooperative, children's home, rural schools project</p>
        <span class="btn-small">Read more</span>
      </article>
      <article class="card">
        <div class="card-image b" role="img" aria-label="Two community members standing outside a village home in Rwanda"></div>
        <p>Sunrise Rwanda – women's self help groups in rural Rwanda</p>
        <span class="btn-small">Read more</span>
      </article>
      <article class="card">
        <div class="card-image c" role="img" aria-label="Women gathered beside a brick building in Mozambique"></div>
        <p>Harvest Mozambique – coaching women NGO leaders from around the country</p>
        <span class="btn-small">Read more</span>
      </article>
    </div>
  </div>
</section>

<section class="stories">
  <div class="wrap">
    <h2 class="section-title">Stories</h2>
    <div class="stories-grid">
      <div class="video" role="img" aria-label="Video still of a community meeting held under a thatched shelter">
        <span class="play"><svg width="18" height="18" viewBox="0 0 18 18"><path d="M5 3 L15 9 L5 15 Z" fill="#fff"/></svg></span>
      </div>
      <div class="story-list">
        <div class="story"><div class="story-thumb a" role="img" aria-label="Young woman working at a village market stall"></div><div class="story-text"><strong>A new start for Sokha, condimentum vitae faucibus in,</strong>sollicitudin sed tortor, a season of steady work and hope.</div></div>
        <div class="story"><div class="story-thumb b" role="img" aria-label="Farmer tending crops in a green field"></div><div class="story-text"><strong>Growing more than maize, condimentum vitae faucibus in,</strong>sollicitudin sed tortor, a group harvest shared by all.</div></div>
        <div class="story"><div class="story-thumb c" role="img" aria-label="Children learning together in a rural classroom"></div><div class="story-text"><strong>Back in the classroom, condimentum vitae faucibus in,</strong>sollicitudin sed tortor, new books for a village school.</div></div>
      </div>
    </div>
    <div class="support">
      <div class="support-box">
        <h3>Online Giving</h3>
        <p>Give once or every month and help our partners plan ahead. Your gift goes straight to the projects you choose to support.</p>
        <span class="btn-outline">Donate now</span>
      </div>
      <div class="support-box">
        <h3>Volunteer Vacancies</h3>
        <p>Share your skills at home or overseas. See the roles our partners need help with this year and how to apply.</p>
        <span class="btn-outline">Read more</span>
      </div>
    </div>
  </div>
</section>

<section class="connect">
  <div class="wrap">
    <h2>Connect With Us</h2>
    <div class="connect-buttons">
      <span class="connect-btn"><svg width="20" height="14" viewBox="0 0 20 14"><rect x="1" y="1" width="18" height="12" fill="none" stroke="#fff" stroke-width="1.6"/><path d="M1 1 L10 8 L19 1" fill="none" stroke="#fff" stroke-width="1.6"/></svg>Email Subscribe</span>
      <span class="connect-btn">Find us on Circlebook</span>
      <span class="connect-btn">View us on Snapgram</span>
    </div>
  </div>
</section>

<footer class="site-footer">
  <div class="wrap footer-cols">
    <div class="footer-col">
      <h4>Quick Links</h4>
      <ul><li>Home</li><li>About Marigold</li><li>Current Projects</li><li>Stories</li><li>Giving</li><li>Volunteer</li><li>Partners</li><li>Contact</li><li>Terms and conditions</li><li>Privacy policy</li><li>Sitemap</li></ul>
    </div>
    <div class="footer-col news">
      <h4>News</h4>
      <ul><li>Project update</li><li>Partner visit</li><li>Annual report</li><li>New school open</li><li>Field notes</li><li>Giving appeal</li><li>Volunteer thanks</li><li>Events</li></ul>
    </div>
    <div class="newsletter">
      <h4 class="footer-col" style="font-size:10px;font-weight:700;color:#fff;margin-bottom:5px">NEWSLETTER</h4>
      <div class="newsletter-form"><span>Email</span><b>Sign up</b></div>
      <div class="social"><i></i><i></i><i></i></div>
    </div>
  </div>
</footer>
<div class="copyright">
  <div class="wrap">Copyright © 2015 The Marigold Venture. All rights reserved.<div class="social"><i></i><i></i></div></div>
</div>

</body>
</html>
```